Business card design for Virtual Assistance company

I need a business card designed for my virtual assistance company. We are a small company who services primarily C-level executive clients. The card needs to be double sided with the following contact information on the back:
Melissa Thornbury
Owner/CEO
info@rkpadvisory.net
www.rkpadvisory.net
555.302.9817

The front side should just have the company name incorporated: "RKP Advisory" and "virtual assistance"

The card should be simplistic, but eye catching and should speak to high level executives. Our primary focus areas consist of executive assistance and government contracting.

Target Market(s)

CEOs and executives

Contact Information for Business Card

see project description. phone, email, website.

Colors

Designer to choose only greyscale colors for use in the design.

```html
<!DOCTYPE html>
<html lang="en">
<head>
<meta charset="utf-8">
<title>RKP Advisory – Business Card</title>
<link rel="stylesheet" href="https://fonts.googleapis.com/css2?family=Cinzel:wght@600&family=Poppins:wght@400;500&display=swap">
<style>
  :root {
    --backdrop: #9b9b9b;
    --paper: #ffffff;
    --charcoal: #2a2a2a;
    --charcoal-deep: #262626;
    --steel: #6f6f6f;
    --mid-grey: #8a8a8a;
    --ink: #2b2b2b;
  }
  * { margin: 0; padding: 0; box-sizing: border-box; }
  html, body { width: 1093px; height: 1200px; overflow: hidden; }
  body { background: var(--backdrop); position: relative; font-family: "Poppins", sans-serif; }

  .card {
    position: absolute;
    left: 264px;
    width: 580px;
    height: 356px;
    border-radius: 22px;
  }
  .card--front { top: 226px; background: var(--paper); }
  .card--back { top: 621px; background: var(--charcoal-deep); }

  .name-bar {
    position: absolute; left: 0; top: 45px;
    width: 16px; height: 33px; background: var(--charcoal);
  }
  .holder { position: absolute; left: 26px; top: 40px; }
  .holder__name {
    font-family: "Cinzel", serif; font-weight: 600;
    font-size: 20px; color: var(--charcoal); line-height: 1.05; letter-spacing: 0.2px;
  }
  .holder__role { font-size: 17px; color: var(--ink); line-height: 1.2; }

  .brand-block {
    position: absolute;
    display: flex; flex-direction: column; align-items: stretch;
  }
  .card--front .brand-block { right: 29px; top: 88px; }
  .card--back .brand-block { left: 50%; top: 142px; transform: translateX(-50%); }

  .brand {
    font-family: "Cinzel", serif; font-weight: 600;
    white-space: nowrap; line-height: 1; text-align: center;
  }
  .card--front .brand { font-size: 27px; color: var(--charcoal); }
  .card--back .brand { font-size: 38px; color: var(--steel); }

  .tagline {
    display: flex; align-items: center; gap: 6px;
    margin-top: 10px;
    font-weight: 500; letter-spacing: 1.6px; white-space: nowrap;
  }
  .tagline::before, .tagline::after {
    content: ""; flex: 1; height: 1.5px; background: currentColor;
  }
  .card--front .tagline { font-size: 10.5px; color: var(--mid-grey); }
  .card--back .tagline { font-size: 14px; color: #4a4a4a; margin-top: 14px; letter-spacing: 2.2px; }

  .contacts { position: absolute; left: 27px; top: 283px; list-style: none; }
  .contacts li {
    display: flex; align-items: center; gap: 7px;
    font-size: 17.5px; color: var(--ink); line-height: 21px;
  }
  .contacts svg { width: 16px; height: 16px; fill: var(--charcoal); flex: none; }

  .website {
    position: absolute; right: 29px; top: 301px;
    font-size: 17.5px; line-height: 21px; color: var(--ink);
  }
</style>
</head>
<body>
  <section class="card card--front" aria-label="Card front">
    <div class="name-bar"></div>
    <div class="holder">
      <p class="holder__name">MELISSA THORNBURY</p>
      <p class="holder__role">Owner/CEO</p>
    </div>
    <div class="brand-block">
      <p class="brand">RKP ADVISORY</p>
      <p class="tagline">VIRTUAL ASSISTANCE</p>
    </div>
    <ul class="contacts">
      <li>
        <svg viewBox="0 0 24 24" aria-hidden="true"><path d="M6.6 10.8a15.1 15.1 0 0 0 6.6 6.6l2.2-2.2a1 1 0 0 1 1-.25 11.4 11.4 0 0 0 3.6.57 1 1 0 0 1 1 1V20a1 1 0 0 1-1 1A17 17 0 0 1 3 4a1 1 0 0 1 1-1h3.5a1 1 0 0 1 1 1c0 1.250.2 2.45.57 3.57a1 1 0 0 1-.25 1z"/></svg>
        555.302.9817
      </li>
      <li>
        <svg viewBox="0 0 24 24" aria-hidden="true"><path d="M2 5h20v14H2z M3.5 6.5 12 13l8.5-6.5" fill="var(--charcoal)" stroke="#fff" stroke-width="1.3"/></svg>
        info@rkpadvisory.net
      </li>
    </ul>
    <p class="website">www.rkpadvisory.net</p>
  </section>

  <section class="card card--back" aria-label="Card back">
    <div class="brand-block">
      <p class="brand">RKP ADVISORY</p>
      <p class="tagline">VIRTUAL ASSISTANCE</p>
    </div>
  </section>
</body>
</html>
```